Home Security check flyer

I am a locksmith company. Wanting a flyer designed for postal delivery to houses.
The design is to have a home security check list similar to the one attached (Not exactly the same) targeting locks with some pictures of deadlocks, Deadbolts, Window Locks, Security door locks Etc..
The idea is to get people in there homes to make sure they are secure and if not to call us for a free quote.
Flyer is to catch customers eye so they don't just throw it our. E.G. IS YOUR HOME SECURE on the front
A4 Size to be folded to twice to envelope size.
My company information can be found at
www.tarvencroftkeys.com.au

Reason: Want to try a few changes on some of the eliminated ones.

Target Market(s)

residential homes (Security)

Industry/Entity Type

Locksmith

Requirements
Must have
• My logo and contact information
Based on information from www.tarvencroftkeys.com.au

```html
<!DOCTYPE html>
<html lang="en">
<head>
<meta charset="utf-8">
<title>Home Security Audit – Tarvencroft Keys</title>
<link href="https://fonts.googleapis.com/css2?family=Arimo:wght@400;700&display=swap" rel="stylesheet">
<style>
:root{
  --red:#c8202f;
  --red-dark:#b01b28;
  --ink:#333;
  --muted:#555;
  --box:#e8848c;
  --paper:#fff;
  --backdrop:#e9e7e4;
}
*{box-sizing:border-box;margin:0;padding:0}
html,body{width:1200px;height:960px;overflow:hidden}
body{background:var(--backdrop);font-family:"Arimo",Arial,sans-serif;color:var(--ink);position:relative}
.page{position:absolute;top:84px;width:560px;height:792px;background:var(--paper);overflow:hidden;box-shadow:0 2px 10px rgba(0,0,0,.15)}
.page--front{left:30px;padding:14px 14px 0;display:flex;flex-direction:column}
.page--back{left:610px}

/* front header */
.masthead{display:flex;align-items:center;gap:22px;height:60px;flex:none}
.brand{display:flex;align-items:center;gap:8px;flex:none}
.brand__mark{width:16px;height:16px;background:var(--red)}
.brand__name{font-size:17px;font-weight:700;color:var(--red);white-space:nowrap}
.masthead__title{font-size:33px;font-weight:700;color:var(--red);white-space:nowrap}
.intro{font-size:10.5px;line-height:1.3;color:var(--muted);padding:8px 8px 0;flex:none}
.intro p{margin-bottom:5px}
.intro p.intro__ask{margin-top:8px}
.condition-bar{display:flex;justify-content:space-between;background:var(--red);color:#fff;font-size:11px;font-weight:700;padding:4px 10px;margin-top:8px;flex:none}

/* audit sections */
.audit-section{border:1.5px solid var(--red);border-top:none;margin-top:3px;padding:2px 8px 3px;flex:none}
.audit-section__title{font-size:13px;line-height:1.25;font-weight:700;color:var(--red)}
.row{display:grid;grid-template-columns:120px 40px 34px 1fr;align-items:center;min-height:17.5px;font-size:9px}
.row__label{color:var(--muted)}
.row__tick{display:flex;align-items:center;gap:4px;color:var(--muted);font-size:8.5px}
.tickbox{display:inline-block;width:13px;height:13px;border:1px solid var(--box)}
.row__note{color:var(--ink);font-size:9px;line-height:1.15}
.row__note--small{font-size:7.5px;color:var(--muted);line-height:1.1}
.row--tall{min-height:22px}

.front-footer{margin:auto -14px 0;height:40px;flex:none;display:flex;justify-content:space-between;align-items:center;padding:0 30px}
.front-footer__slogan{font-size:14px;color:var(--red)}
.front-footer__web{font-size:10.5px;color:var(--red)}

/* back */
.product-band{height:168px;background:var(--red);padding:14px 14px 0}
.product-band__photos{width:100%;height:140px;background:linear-gradient(90deg,#c9ccd0,#9fa4aa,#d7d9dc,#8f949a,#cfd2d6);opacity:.55;border-radius:4px}
.other{padding:10px 36px 0}
.other__title{font-size:9px;font-weight:700;margin-bottom:4px}
.other .row{grid-template-columns:112px 42px 40px 1fr;min-height:19.5px;font-size:9px}
.other .row__note{font-size:6.8px;line-height:1.2}
.personal{padding:8px 36px 0 38px}
.personal__title{font-size:12px;font-weight:700;margin-bottom:6px}
.question{display:grid;grid-template-columns:1fr 44px 30px;margin-bottom:9px}
.question__head{font-size:11px;margin-bottom:1px}
.question__text{font-size:7.4px;line-height:1.45;color:var(--muted)}
.question .row__tick{align-items:flex-start;padding-top:2px}
.disclaimer{display:flex;justify-content:space-between;align-items:flex-start;padding:16px 36px 0}
.disclaimer__text{font-size:7px;line-height:2.1;width:290px}
.disclaimer__badge{width:52px;height:52px;border-radius:50%;background:var(--red-dark);margin-right:4px}
.back-footer{position:absolute;left:0;right:0;bottom:0;height:64px;background:var(--red);display:flex;justify-content:space-between;align-items:center;padding:4px 28px 0 32px;color:#fff}
.back-footer__slogan{font-size:14px}
.back-footer__web{font-size:10.5px}
.back-footer::before{content:"";position:absolute;left:0;right:0;top:8px;height:1px;background:rgba(255,255,255,.6)}
</style>
</head>
<body>

<section class="page page--front">
  <header class="masthead">
    <div class="brand"><span class="brand__mark"></span><span class="brand__name">Tarvencroft Keys</span></div>
    <h1 class="masthead__title">Home Security Audit</h1>
  </header>
  <div class="intro">
    <p>House-breaking is one if the most comon crimes and can occur at any time day or night. This checklist is designed to help you take a fresh look at your security.</p>
    <p>You can take steps to reduce identified risk areas in your home and reduce the likelihood of becoming a victim of crime or a repeat victim of crime.</p>
    <p class="intro__ask">How does your home security rate?</p>
  </div>
  <div class="condition-bar"><span>PRESENT CONDITION</span><span>Consider making changes to the items ticked NO</span></div>

  <div class="audit-section">
    <h2 class="audit-section__title">Security Doors</h2>
    <div class="row"><span class="row__label">At all entry/exits?</span><span class="row__tick">Y <i class="tickbox"></i></span><span class="row__tick">N <i class="tickbox"></i></span><span class="row__note">Security doors deter intruders from entering your home</span></div>
    <div class="row"><span class="row__label">Finger guards?</span><span class="row__tick">Y <i class="tickbox"></i></span><span class="row__tick">N <i class="tickbox"></i></span><span class="row__note">Finger guards prevent the lock on your security door/s being tampered with</span></div>
    <div class="row"><span class="row__label">Triple locks?</span><span class="row__tick">Y <i class="tickbox"></i></span><span class="row__tick">N <i class="tickbox"></i></span><span class="row__note">Triple locks increase the strength and security of your doors</span></div>
  </div>

  <div class="audit-section">
    <h2 class="audit-section__title">Main Entry/Exit Doors</h2>
    <div class="row"><span class="row__label">Front - solid core?</span><span class="row__tick">Y <i class="tickbox"></i></span><span class="row__tick">N <i class="tickbox"></i></span><span class="row__note">Solid doors are preferred; the door should be as strong as the lock</span></div>
    <div class="row"><span class="row__label">Front - viewer?</span><span class="row__tick">Y <i class="tickbox"></i></span><span class="row__tick">N <i class="tickbox"></i></span><span class="row__note">Door viewers help you see who is outside your front door before you o</span></div>
    <div class="row"><span class="row__label">Back - solid core?</span><span class="row__tick">Y <i class="tickbox"></i></span><span class="row__tick">N <i class="tickbox"></i></span><span class="row__note">solid doors are preferred; hollow core doors should be avoided</span></div>
    <div class="row"><span class="row__label">Adequate locks?</span><span class="row__tick">Y <i class="tickbox"></i></span><span class="row__tick">N <i class="tickbox"></i></span><span class="row__note">Dead locks are the best type of lock to use on entry/exit doors</span></div>
    <div class="row"><span class="row__label">Keyed alike?</span><span class="row__tick">Y <i class="tickbox"></i></span><span class="row__tick">N <i class="tickbox"></i></span><span class="row__note">for safety and ease of use, one key opens all doors</span></div>
  </div>

  <div class="audit-section">
    <h2 class="audit-section__title">Sliding doors</h2>
    <div class="row"><span class="row__label">Patio bolts?</span><span class="row__tick">Y <i class="tickbox"></i></span><span class="row__tick">N <i class="tickbox"></i></span><span class="row__note">Keyed patio bolts on sliding doors strengthen the security of these doors</span></div>
  </div>

  <div class="audit-section">
    <h2 class="audit-section__title">Windows</h2>
    <div class="row"><span class="row__label">Key operated locks?</span><span class="row__tick">Y <i class="tickbox"></i></span><span class="row__tick">N <i class="tickbox"></i></span><span class="row__note">Key operated locks strengthen the security of your windows</span></div>
    <div class="row"><span class="row__label">Keyed alike?</span><span class="row__tick">Y <i class="tickbox"></i></span><span class="row__tick">N <i class="tickbox"></i></span><span class="row__note">For safety and ease of use, one key opens all windows</span></div>
    <div class="row"><span class="row__label">Security screens?</span><span class="row__tick">Y <i class="tickbox"></i></span><span class="row__tick">N <i class="tickbox"></i></span><span class="row__note">Security screens, grilles and shutters allow ventilation and can provide security</span></div>
    <div class="row"><span class="row__label">Warning Stickers?</span><span class="row__tick">Y <i class="tickbox"></i></span><span class="row__tick">N <i class="tickbox"></i></span><span class="row__note">Warinng stickers may deter intruders from stealing your property</span></div>
  </div>

  <div class="audit-section">
    <h2 class="audit-section__title">Lighting</h2>
    <div class="row"><span class="row__label">Main entry/exits?</span><span class="row__tick">Y <i class="tickbox"></i></span><span class="row__tick">N <i class="tickbox"></i></span><span class="row__note">The main entry/exit areas to your home should be well lit</span></div>
    <div class="row"><span class="row__label">Timers fitted?</span><span class="row__tick">Y <i class="tickbox"></i></span><span class="row__tick">N <i class="tickbox"></i></span><span class="row__note">Lighta left on inside your home when you are out often deter intruder</span></div>
    <div class="row"><span class="row__label">Timers used?</span><span class="row__tick">Y <i class="tickbox"></i></span><span class="row__tick">N <i class="tickbox"></i></span><span class="row__note">Timers should be activated when away from your home at night</span></div>
    <div class="row"><span class="row__label">Sensor lighting?</span><span class="row__tick">Y <i class="tickbox"></i></span><span class="row__tick">N <i class="tickbox"></i></span><span class="row__note">Sensor lighting in ‘ high risk’ areas deter intruders from entering your home</span></div>
  </div>

  <div class="audit-section">
    <h2 class="audit-section__title">Property Marking</h2>
    <div class="row row--tall"><span class="row__label">Engraved with code?</span><span class="row__tick">Y <i class="tickbox"></i></span><span class="row__tick">N <i class="tickbox"></i></span><span class="row__note row__note--small">Property engraving and using WARNING stickers on your property reduces the risk of it being stolen</span></div>
    <div class="row row--tall"><span class="row__label">Code recorded?</span><span class="row__tick">Y <i class="tickbox"></i></span><span class="row__tick">N <i class="tickbox"></i></span><span class="row__note row__note--small">Your property ID code should be recorded with police to assist them to contact owners of recovered items</span></div>
    <div class="row row--tall"><span class="row__label">Inventory list?</span><span class="row__tick">Y <i class="tickbox"></i></span><span class="row__tick">N <i class="tickbox"></i></span><span class="row__note row__note--small">Recording serial numbers, makes, models and descriptions of your property helps police recover stolen items and will assist you to make an insurance claim (you may wish to photograph items and store somewhere safe)</span></div>
  </div>

  <footer class="front-footer">
    <span class="front-footer__slogan">COMMUNITY SAFETY AND CRIME PREVENTION</span>
    <span class="front-footer__web">www.tarvencroftkeys.com.au</span>
  </footer>
</section>

<section class="page page--back">
  <div class="product-band">
    <div class="product-band__photos" role="img" aria-label="Product photos of door knob locks, a keypad lock, a gate latch, a deadbolt and rim deadlocks"></div>
  </div>

  <div class="other">
    <h2 class="other__title">Other safety considerations</h2>
    <div class="row"><span class="row__label">Clear vision?</span><span class="row__tick">Y <i class="tickbox"></i></span><span class="row__tick">N <i class="tickbox"></i></span><span class="row__note">Make sure all doors and windoes can be seen clearly from outside</span></div>
    <div class="row"><span class="row__label">Trees/shrubs trimmed?</span><span class="row__tick">Y <i class="tickbox"></i></span><span class="row__tick">N <i class="tickbox"></i></span><span class="row__note">Trim any trees/shrubs that conceal doors and windows from being observed from the street</span></div>
    <div class="row"><span class="row__label">Garage/shed secure?</span><span class="row__tick">Y <i class="tickbox"></i></span><span class="row__tick">N <i class="tickbox"></i></span><span class="row__note">Garages and sheds should be securely locked at all time</span></div>
    <div class="row"><span class="row__label">Tools secure?</span><span class="row__tick">Y <i class="tickbox"></i></span><span class="row__tick">N <i class="tickbox"></i></span><span class="row__note">Lock tools away to prevent an intruder using them to get into your house</span></div>
    <div class="row"><span class="row__label">Whwwlie bins secured?</span><span class="row__tick">Y <i class="tickbox"></i></span><span class="row__tick">N <i class="tickbox"></i></span><span class="row__note">Lock whwwlie bins away or chain them to a fixed structure away from the house to prevent an intruder using them to climb into your home</span></div>
    <div class="row"><span class="row__label">Gates to yard secured?</span><span class="row__tick">Y <i class="tickbox"></i></span><span class="row__tick">N <i class="tickbox"></i></span><span class="row__note">Lock gates to the backyard with a keyed padlock to prevent access by intruders</span></div>
    <div class="row"><span class="row__label">Meter box secured?</span><span class="row__tick">Y <i class="tickbox"></i></span><span class="row__tick">N <i class="tickbox"></i></span><span class="row__note">Your electricity meter box should be locked (Contact your electricity provider to arrange)</span></div>
    <div class="row"><span class="row__label">House numbers?</span><span class="row__tick">Y <i class="tickbox"></i></span><span class="row__tick">N <i class="tickbox"></i></span><span class="row__note">House numbers should be clearly visible from the road</span></div>
    <div class="row"><span class="row__label">Smoke alarms?</span><span class="row__tick">Y <i class="tickbox"></i></span><span class="row__tick">N <i class="tickbox"></i></span><span class="row__note">Install smoke alarms and develop a frie evacuation plan</span></div>
    <div class="row"><span class="row__label">Security alarms?</span><span class="row__tick">Y <i class="tickbox"></i></span><span class="row__tick">N <i class="tickbox"></i></span><span class="row__note">Electronic security alarm systems deter intruders from entering your home</span></div>
    <div class="row"><span class="row__label">Safe disposal of personal documents?</span><span class="row__tick">Y <i class="tickbox"></i></span><span class="row__tick">N <i class="tickbox"></i></span><span class="row__note">All documents/ paperwork containing your personal details (e.g. old phone bills, medical invoices, power bills rates notices) should be totally destroyed before being placed in your wheelie bin for rubbish collection. This will help protect you from identity theft. For more information on this refer to the NPS Identity Theft fact sheet.</span></div>
  </div>

  <div class="personal">
    <h2 class="personal__title">Personal Security in the Home</h2>
    <div class="question">
      <div><p class="question__head">Do you keep information about your security arrangements private?</p><p class="question__text">Be aware of providing about your home security arrangements to people that do not need to know this information. Highlighting your security weaknesses to others could be detrimental.</p></div>
      <span class="row__tick">Y <i class="tickbox"></i></span><span class="row__tick">N <i class="tickbox"></i></span>
    </div>
    <div class="question">
      <div><p class="question__head">Do you keep information about your personal arrangements private?</p><p class="question__text">Information about bank accounts and balances and personal particulars, including your living arrangements, should not be disclosed unnecessarily. Be conscious of also providing information to others about your planned absences from home.</p></div>
      <span class="row__tick">Y <i class="tickbox"></i></span><span class="row__tick">N <i class="tickbox"></i></span>
    </div>
    <div class="question">
      <div><p class="question__head">Do you store valuables out of sight and reach from outside?</p><p class="question__text">Oppertunistic thefts can occur when valuables are in clear view and within easy reach reach. valuables are best stored out of sight and in a secure location.</p></div>
      <span class="row__tick">Y <i class="tickbox"></i></span><span class="row__tick">N <i class="tickbox"></i></span>
    </div>
    <div class="question">
      <div><p class="question__head">Do you have important phone numbers stored in your phone?</p><p class="question__text">Having your local police station number stored in your phone makes it easier to dial, especially in the dark. 000 (triple zero) can also be stored for use in emergencies. It is also useful to store the phone numbers of family and close friends for use by emergency services in the event of an incident.</p></div>
      <span class="row__tick">Y <i class="tickbox"></i></span><span class="row__tick">N <i class="tickbox"></i></span>
    </div>
  </div>

  <div class="disclaimer">
    <p class="disclaimer__text">DISCLAIMER: This fact sheet contains general guidelines only. The Northvale Police Service in providing this information makes no representations nor gives any warranty or guarantee concerning the safety of persons or property.</p>
    <span class="disclaimer__badge" role="img" aria-label="Trade association membership badge"></span>
  </div>

  <footer class="back-footer">
    <span class="back-footer__slogan">COMMUNITY SAFETY AND CRIME PREVENTION</span>
    <span class="back-footer__web">www.tarvencroftkeys.com.au</span>
  </footer>
</section>

</body>
</html>
```